Financial Advisor Resource Firm needs business card design

Need business card design for company in Omaha NE called Meridale Circle. We provide resources to financial advisors....workshop programs, retirement analysis, and insurance planning. I would like to see designs that use grays, greens, black, and white colors. The final design should communicate 'collaboration' and be simple yet attractive to financial planning clients. I will attached our logo and another picture of a puzzle piece coming together. I would like the incorporate the puzzle picture somehow, maybe on the back somehow, with color or just the gray scale....OR, the picture be the front of the card with 'Meridale' definition on it (see upload) and then company logo, employee name, title, address on the back (see ppt uploaded). The following disclosure needs to be included somewhere- Advisory services offered through Stonebrook Assets, LLC.
Updates

I uploaded a svg and ai file of the logo

Target Market(s)

Financial planning clients and financial advisors....so pretty diverse age range of about 40-70.

Industry/Entity Type

Financial Planning

Contact Information for Business Card

Tobias L. Fenwright, MBA
Founder/President
5287 E. Larkin Road
Suite 230
Omaha, NE 68190
Phone- (402) 555-0147
Cell- (402) 555-0183
Fax- (402) 555-0129
email- tobias@meridaleplan.example
web address- www.meridaleplan.example

Colors
1b1b1b
474747
d3d3d3
ffffff
9bcb3c
abd036

Requirements
Must have
• Must include logo provided, must be 2 sided, and must have disclosure...all of these items listed in project description

```html
<!DOCTYPE html>
<html lang="en">
<head>
<meta charset="utf-8">
<title>Meridale Circle – Business Card</title>
<link rel="stylesheet" href="https://fonts.googleapis.com/css2?family=Roboto:wght@400;500&display=swap">
<style>
  :root {
    --canvas: #f4f4f4;
    --card: #232323;
    --ink: #1b1b1b;
    --gray: #474747;
    --silver: #d3d3d3;
    --muted: #9a9a9a;
    --white: #ffffff;
    --green: #9bcb3c;
    --green-alt: #abd036;
  }
  * { margin: 0; padding: 0; box-sizing: border-box; }
  html, body { width: 1200px; height: 900px; overflow: hidden; }
  body {
    background: var(--canvas);
    font-family: "Roboto", sans-serif;
    position: relative;
  }
  .card {
    position: absolute;
    width: 598px;
    height: 341px;
    background: var(--card);
    box-shadow: 0 14px 30px rgba(0,0,0,.28);
    overflow: hidden;
  }
  .card--front { left: 302px; top: 97px; }
  .card--back  { left: 301px; top: 479px; }

  .wordmark {
    display: flex;
    align-items: center;
    gap: 10px;
    font-weight: 500;
    letter-spacing: 2px;
    text-transform: uppercase;
    white-space: nowrap;
  }
  .wordmark__dot {
    width: 14px; height: 14px;
    border-radius: 50%;
    background: var(--green);
  }
  .card--front .wordmark {
    position: absolute;
    left: 0; right: 0; top: 156px;
    justify-content: center;
    font-size: 34px;
    color: var(--silver);
  }
  .tagline {
    position: absolute;
    left: 0; right: 0; top: 276px;
    text-align: center;
    font-size: 14px;
    color: var(--white);
  }
  .website {
    position: absolute;
    left: 0; right: 0; top: 299px;
    text-align: center;
    font-size: 15px;
    color: var(--white);
  }
  .disclosure {
    position: absolute;
    left: 0; right: 0; top: 322px;
    text-align: center;
    font-size: 9px;
    color: var(--muted);
  }
  .accent { color: var(--green); }

  .back-art { position: absolute; inset: 0; }
  .card--back .wordmark {
    position: absolute;
    left: 44px; top: 198px;
    font-size: 20px;
    color: var(--white);
  }
  .card--back .wordmark__dot { width: 10px; height: 10px; }

  .person { position: absolute; left: 312px; top: 106px; }
  .person__name {
    font-size: 21px;
    font-weight: 500;
    color: var(--green);
  }
  .person__credential { font-size: 13px; color: var(--white); font-weight: 400; }
  .person__title { font-size: 14px; color: var(--white); margin-top: 3px; }

  .contacts {
    position: absolute;
    left: 312px; top: 170px;
    list-style: none;
  }
  .contacts li {
    display: flex;
    align-items: center;
    gap: 10px;
    height: 24px;
    font-size: 15px;
    color: var(--white);
  }
  .contacts svg { width: 18px; height: 18px; fill: var(--green); flex: none; }

  .address {
    position: absolute;
    left: 0; right: 0; top: 297px;
    text-align: center;
    font-size: 15.5px;
    color: var(--green);
  }
</style>
</head>
<body>

<section class="card card--front">
  <div class="wordmark"><span class="wordmark__dot"></span>Meridale Circle</div>
  <p class="tagline">To come <span class="accent">TOGETHER</span> and <span class="accent">UNITE</span> in common interest and <span class="accent">FOCUS</span></p>
  <p class="website">www.<span class="accent">meridaleplan</span>.example</p>
  <p class="disclosure">Advisory services offered through Stonebrook Assets, LLC.</p>
</section>

<section class="card card--back">
  <svg class="back-art" viewBox="0 0 598 341" width="598" height="341">
    <defs>
      <linearGradient id="photo-tone" x1="0" y1="0" x2="1" y2="1">
        <stop offset="0" stop-color="#6f9a3a"/>
        <stop offset=".5" stop-color="#8fbf4a"/>
        <stop offset="1" stop-color="#3f5a24"/>
      </linearGradient>
    </defs>
    <path role="img" aria-label="Green-toned photo of hands joining puzzle pieces"
          fill="url(#photo-tone)"
          d="M0,0 H598 V16 C470,4 380,40 300,92 C220,148 120,176 0,182 Z"/>
    <path fill="var(--green)"
          d="M322,72 C420,18 540,12 598,52 V66 C540,30 430,36 336,74 Z"/>
  </svg>

  <div class="wordmark"><span class="wordmark__dot"></span>Meridale Circle</div>

  <div class="person">
    <p class="person__name">Tobias L. Fenwright<span class="person__credential">, MBA</span></p>
    <p class="person__title">Founder | President</p>
  </div>

  <ul class="contacts">
    <li>
      <svg viewBox="0 0 24 24" aria-hidden="true"><path d="M6.6 10.8c1.4 2.8 3.8 5.1 6.6 6.6l2.2-2.2c.3-.3.7-.4 1-.2 1.1.4 2.300.6 3.6.6.6 0 1 .4 1 1V20c0 .6-.4 1-1 1C10.6 21 3 13.4 3 4c0-.6.4-1 1-1h3.5c.6 0 1 .4 1 1 0 1.3.2 2.5.6 3.6.1.3 0 .7-.2 1z"/></svg>
      (402) 555 - 0147
    </li>
    <li>
      <svg viewBox="0 0 24 24" aria-hidden="true"><path d="M8 2h8a2 2 0 0 1 2 2v16a2 2 0 0 1-2 2H8a2 2 0 0 1-2-2V4a2 2 0 0 1 2-2zm0 3v12h8V5zm4 13.2a1 1 0 1 0 0 2 1 1 0 0 0 0-2z"/></svg>
      (402) 555 - 0183
    </li>
    <li>
      <svg viewBox="0 0 24 24" aria-hidden="true"><path d="M3 7h4v14H3zm6-4h9l3 3v15H9zm2 8v2h2v-2zm4 0v2h2v-2zm-4 4v2h2v-2zm4 0v2h2v-2zM11 5v4h8V6.8L17.2 5z"/></svg>
      (402) 555 - 0129
    </li>
    <li>
      <svg viewBox="0 0 24 24" aria-hidden="true"><path d="M3 5h18v14H3zm2 2v.5l7 4.5 7-4.5V7z"/></svg>
      tobias@meridaleplan.example
    </li>
  </ul>

  <p class="address">5287 E. Larkin Road Suite 230, Omaha, NE 68190</p>
</section>

</body>
</html>
```